Can you make our site AWESOME?

Hi Guys,

I am a co-founder of Tallow Crate Rentals Australia, the world's first e-commerce skip bin business.

We are looking to update our site before a launch into the UK in March.

Please help us by submitting your designs for the following pages:

- Home page (www.tallowcraterentals.example.au)
- About us (https://www.tallowcraterentals.example.au/pages/about-us
- Contact us (https://www.tallowcraterentals.example.au/pages/contact-us)
- Quick Quote / Pricing (https://www.tallowcraterentals.example.au/pages/free-instant-quote-skip-bin-hire)

NOTES:
- Design should be high-converting
- best designs will be fresh, modern, easy to read, distinctive and memorable
- please use our logo and video colours
- feel free to change logos, layout, images and anything else you feel can be improved
- the winning designer will potentially have the opportunity to re-design the other pages on our site
- brief is for design only

Any questions just ask.

Thanks,
Oliver

```html
<!DOCTYPE html>
<html lang="en">
<head>
<meta charset="utf-8">
<title>Tallow Crate Rentals Australia</title>
<link href="https://fonts.googleapis.com/css2?family=Poppins:wght@300;400;500;600;700&display=swap" rel="stylesheet">
<style>
:root{
  --purple:#5a5e9c;
  --purple-dark:#3c4075;
  --purple-deep:#2f3262;
  --green:#3bb54a;
  --ink:#2e3060;
  --text:#555;
  --light:#f3f3f7;
  --footer:#333336;
  --footer-deep:#222225;
  --white:#fff;
}
*{box-sizing:border-box;margin:0;padding:0}
html,body{width:1200px;height:3727px;overflow:hidden}
body{font-family:'Poppins',sans-serif;color:var(--text);background:var(--white);position:relative}
.abs{position:absolute}
.center{text-align:center;left:0;width:1200px}

/* header */
.site-header{position:absolute;top:0;left:0;width:1200px;height:90px;background:var(--white)}
.brand{position:absolute;left:89px;top:20px;display:flex;align-items:center;gap:12px}
.brand-mark{width:40px;height:40px;background:var(--purple)}
.brand-name{font-weight:700;font-size:17px;color:var(--purple);line-height:1.15;width:200px}
.nav{position:absolute;top:28px;font-size:12px;font-weight:500;color:var(--ink);letter-spacing:.3px}
.call-btn{position:absolute;left:919px;top:0;width:191px;height:32px;background:var(--purple);color:#fff;font-size:12px;font-weight:600;border-radius:0 0 10px 10px;text-align:center;line-height:32px}
.login{position:absolute;left:919px;top:48px;width:191px;text-align:center;font-size:11px;font-weight:600;color:var(--green)}

/* hero */
.hero{position:absolute;top:90px;left:0;width:1200px;height:640px;background:linear-gradient(180deg,#6b6fb0 0%,#4b4f8c 60%,#393d72 100%);overflow:hidden}
.skyline{position:absolute;left:0;bottom:0;width:1200px;height:260px;background:linear-gradient(180deg,rgba(40,44,95,.0),rgba(40,44,95,.75))}
.hero-title{top:176px;font-size:40px;font-weight:600;color:#fff}
.hero-sub{top:258px;font-size:19px;color:#e6e7f5;font-weight:300}
.hero-label{top:318px;font-size:13px;font-weight:600;color:#fff}
.search{position:absolute;display:flex;height:57px;border-radius:30px;overflow:hidden;background:#fff}
.search .field{flex:1;padding-left:30px;line-height:57px;font-size:15px;color:#888}
.search .go{width:124px;background:var(--green);color:#fff;font-size:13px;font-weight:600;display:flex;align-items:center;justify-content:center;gap:8px;border-radius:30px}
.hero-curve{position:absolute;left:0;top:640px;width:1200px;height:60px}

/* categories */
.cat{position:absolute;top:556px;width:159px;height:159px;background:#fff;border-radius:6px;box-shadow:0 6px 20px rgba(0,0,0,.12);text-align:center}
.cat .icon{width:52px;height:52px;margin:30px auto 24px;border:3px solid var(--green);border-radius:8px}
.cat .label{font-size:12px;font-weight:600;color:var(--ink)}

/* video */
.section-title{font-size:27px;font-weight:400;color:var(--ink);line-height:1.3}
.video-band{position:absolute;top:1100px;left:0;width:1200px;height:260px;background:var(--light)}
.video{position:absolute;left:241px;top:882px;width:735px;height:392px;background:linear-gradient(160deg,#7a7db8 0%,#5c5f98 55%,#6fae5d 100%);box-shadow:0 6px 20px rgba(0,0,0,.18)}
.play{position:absolute;left:327px;top:156px;width:82px;height:82px;border-radius:50%;background:#fff}

/* steps */
.step{position:absolute;top:1483px;height:151px;background:#fff;border-radius:4px;box-shadow:0 4px 16px rgba(0,0,0,.1);padding:20px 18px 0 100px}
.step .icon{position:absolute;left:22px;top:24px;width:56px;height:56px;border:3px solid var(--green);border-radius:8px}
.step .num{position:absolute;left:30px;bottom:6px;font-size:46px;color:#e6e6ea;font-weight:400;line-height:1}
.step h3{font-size:21px;font-weight:600;color:var(--ink);margin-bottom:6px}
.step p{font-size:12.5px;line-height:1.6;color:#444}
.step p b{color:var(--green);font-weight:500}

.manage{top:1736px;font-size:19px;color:var(--ink);line-height:1.35}

/* testimonials */
.reviews{position:absolute;top:1838px;left:0;width:1200px;height:703px;background:linear-gradient(180deg,#6266a6,#3f4379 70%,#34376a)}
.reviews .section-title{color:#fff;position:absolute;top:56px;width:1200px;text-align:center;font-size:30px;font-weight:300}
.review{position:absolute;top:167px;height:407px;background:#fff;padding:78px 48px 0 54px}
.review .quote{position:absolute;left:36px;top:-20px;width:32px;height:42px;background:#fff;border-radius:50% 50% 50% 0}
.review p{font-size:13px;line-height:2;color:#444}
.review .rule{position:absolute;left:54px;right:48px;top:308px;height:1px;background:#e4e4e4}
.review .who{position:absolute;left:54px;top:334px;display:flex;align-items:center;gap:12px;font-size:15px;color:var(--green)}
.review .avatar{width:30px;height:30px;border-radius:50%;background:#b59a86}
.dots{position:absolute;top:614px;left:590px;display:flex;gap:5px}
.dots i{width:6px;height:6px;border-radius:50%;background:#8e91c4}
.dots i:first-child{background:#4ea0ff}

/* features */
.feature{position:absolute;top:2660px;width:260px;text-align:center}
.feature .icon{width:64px;height:54px;margin:0 auto 30px;border:3px solid var(--green);border-radius:10px}
.feature h4{font-size:15px;font-weight:600;color:var(--ink);margin-bottom:8px}
.feature p{font-size:12.5px;line-height:1.9;color:#444}

/* cta */
.cta{position:absolute;top:2961px;left:0;width:1200px;height:400px;background:linear-gradient(180deg,#6a6eae,#4a4e8b);overflow:hidden}
.cta .skyline{height:230px}
.cta-title{top:62px;font-size:32px;font-weight:500;color:#fff}
.cta-text{top:118px;font-size:15px;color:#fff}
.cta-label{top:166px;font-size:11px;font-weight:600;color:#fff}

/* footer */
.footer{position:absolute;top:3341px;left:0;width:1200px;height:278px;background:var(--footer)}
.hill{position:absolute;left:0;top:3230px;width:1200px;height:115px}
.f-col{position:absolute;top:31px;font-size:12px;line-height:26px;color:#eee}
.news{position:absolute;left:715px;top:24px;font-size:12px;line-height:20px;color:#eee;width:360px}
.sub{position:absolute;left:715px;top:100px;width:358px;height:42px;border-radius:22px;background:#fff;display:flex;overflow:hidden}
.sub .field{flex:1;padding-left:22px;line-height:42px;font-size:13px;color:#555}
.sub .go{width:130px;background:var(--green);color:#fff;font-size:12px;font-weight:600;text-align:center;line-height:42px;border-radius:22px}
.social{position:absolute;left:722px;top:164px;display:flex;gap:36px}
.social i{width:14px;height:14px;border-radius:50%;background:#ddd;display:block}
.bottom{position:absolute;top:3619px;left:0;width:1200px;height:108px;background:var(--footer-deep)}
.copy{position:absolute;left:94px;top:26px;font-size:11px;color:#ddd}
.pay{position:absolute;left:842px;top:20px;display:flex;gap:14px}
.pay i{width:36px;height:24px;border-radius:3px;background:#cfcfd6;display:block}
</style>
</head>
<body>

<header class="site-header">
  <div class="brand"><span class="brand-mark"></span><span class="brand-name">TALLOW CRATE RENTALS AUSTRALIA</span></div>
  <span class="nav" style="left:408px">PRICING</span>
  <span class="nav" style="left:500px">LEARN MORE</span>
  <span class="nav" style="left:628px">ABOUT</span>
  <span class="nav" style="left:706px">TRADE SECRETS</span>
  <span class="nav" style="left:832px">CONTACT</span>
  <div class="call-btn">CALL NOW: 1800 555 019</div>
  <div class="login">LOGIN / CREATE ACCOUNT</div>
</header>

<section class="hero">
  <div class="skyline" role="img" aria-label="City skyline illustration"></div>
  <h1 class="abs center hero-title" style="top:86px">1000's of Skips at Your Finger Tips</h1>
  <p class="abs center hero-sub" style="top:168px">Best Service &amp; Price | Hassle Free | Australia Wide</p>
  <p class="abs center hero-label" style="top:228px">Instant Quote</p>
  <div class="search" style="left:320px;top:278px;width:562px">
    <span class="field">Enter postcode or suburb</span>
    <span class="go"><svg width="13" height="13" viewBox="0 0 14 14"><circle cx="6" cy="6" r="4.5" fill="none" stroke="#fff" stroke-width="2"/><path d="M9.5 9.5L13 13" stroke="#fff" stroke-width="2"/></svg>SEARCH</span>
  </div>
  <svg class="hero-curve" style="top:585px" viewBox="0 0 1200 60" preserveAspectRatio="none"><path d="M0 40 Q600 -10 1200 40 L1200 60 L0 60Z" fill="#fff"/></svg>
</section>

<div class="cat" style="left:165px"><div class="icon" role="img" aria-label="Renovator icon"></div><div class="label">RENOVATOR</div></div>
<div class="cat" style="left:341px"><div class="icon" role="img" aria-label="Tradie icon"></div><div class="label">TRADIE</div></div>
<div class="cat" style="left:521px"><div class="icon" role="img" aria-label="Builder icon"></div><div class="label">BUILDER</div></div>
<div class="cat" style="left:698px"><div class="icon" role="img" aria-label="Corporate icon"></div><div class="label">CORPORATE</div></div>
<div class="cat" style="left:875px"><div class="icon" role="img" aria-label="National icon"></div><div class="label">NATIONAL</div></div>

<h2 class="abs center section-title" style="top:770px">Australia's Highest Rated Skip Bin<br>Hire Company - Rated by You</h2>

<div class="video-band"></div>
<div class="video" role="img" aria-label="Animated video still of a man outside a house asking where his skip bin is">
  <div class="play"><svg width="82" height="82" viewBox="0 0 82 82"><path d="M34 27L56 41L34 55Z" fill="#4a4e8b"/></svg></div>
</div>

<h2 class="abs center section-title" style="top:1390px">As Easy As 1, 2, 3...</h2>

<div class="step" style="left:77px;width:335px">
  <div class="icon" role="img" aria-label="Booking chat icon"></div><span class="num">1</span>
  <h3>Simple, Easy Booking</h3>
  <p>Call <b>1800 555 019</b> or <b>click here</b> to get started with your instant quote</p>
</div>
<div class="step" style="left:435px;width:335px">
  <div class="icon" role="img" aria-label="Confirmation icon"></div><span class="num">2</span>
  <h3>Instant Confirmation</h3>
  <p>Receive your booking details and a 30 minute courtesy call before drop off</p>
</div>
<div class="step" style="left:787px;width:348px">
  <div class="icon" role="img" aria-label="Collection box icon"></div><span class="num">3</span>
  <h3>Gone When Your Ready!</h3>
  <p>Let us know and your bin will be gone within 24hrs</p>
</div>

<p class="abs center manage">We manage your booking from start to finish,<br>so you can focus on other things</p>

<section class="reviews">
  <h2 class="section-title">Five Star Service</h2>
  <div class="review" style="left:92px;width:315px"><span class="quote"></span>
    <p>There are many variations of passages of available but the majority have suffer alteration in some form by inject humour or random words which don't look even slightly believe you are going middle of text.</p>
    <span class="rule"></span><div class="who"><span class="avatar"></span>Kieran Malley</div></div>
  <div class="review" style="left:445px;width:315px"><span class="quote"></span>
    <p>There are many variations of passages of available but the majority have suffer alteration in some form by inject humour or random words which don't look even slightly believe you are going middle of text.</p>
    <span class="rule"></span><div class="who"><span class="avatar"></span>Jessamy Brook</div></div>
  <div class="review" style="left:795px;width:340px"><span class="quote"></span>
    <p>There are many variations of passages of available but the majority have suffer alteration in some form by inject humour or random words which don't look even slightly believe you are going middle of text.</p>
    <span class="rule"></span><div class="who"><span class="avatar"></span>Paulo Smyth</div></div>
  <div class="dots"><i></i><i></i><i></i></div>
</section>

<h2 class="abs center section-title" style="top:2551px">Save Time. Save Money.</h2>

<div class="feature" style="left:44px"><div class="icon" role="img" aria-label="Delivery truck icon"></div><h4>Any Bin, Anytime, Anywhere</h4><p>We connect you with local companies Australia wide; for faster response times, less km's and emissions, greater reliability and lower prices</p></div>
<div class="feature" style="left:337px"><div class="icon" role="img" aria-label="Support agent icon"></div><h4>Service Guaranteed</h4><p>Want to speak to someone when it suits you? We answer the phones and return calls from 7.30am to 8pm 7 days a week</p></div>
<div class="feature" style="left:625px"><div class="icon" role="img" aria-label="Pricing icon"></div><h4>Best Pricing</h4><p>We've done the hard work behind the scenes, so with one click you have your best priced, local skip</p></div>
<div class="feature" style="left:901px"><div class="icon" role="img" aria-label="Partnership icon"></div><h4>First Class Supply Partners</h4><p>Our local supply partners are the best in the business and share our passion for making you happy</p></div>

<section class="cta">
  <div class="skyline" role="img" aria-label="City skyline illustration"></div>
  <h2 class="abs center cta-title">We're ready to go!</h2>
  <p class="abs center cta-text">To book, ask questions or just for a chat, call us 7 days a week, 7.30am to 8pm</p>
  <p class="abs center cta-label">QUICK QUOTE</p>
  <div class="search" style="left:340px;top:201px;width:562px">
    <span class="field">Enter postcode or suburb</span>
    <span class="go"><svg width="13" height="13" viewBox="0 0 14 14"><circle cx="6" cy="6" r="4.5" fill="none" stroke="#fff" stroke-width="2"/><path d="M9.5 9.5L13 13" stroke="#fff" stroke-width="2"/></svg>SEARCH</span>
  </div>
</section>
<svg class="hill" viewBox="0 0 1200 115" preserveAspectRatio="none"><path d="M0 80 C150 20 260 30 380 70 C520 115 640 10 800 40 C930 65 1050 110 1200 60 L1200 115 L0 115Z" fill="#333336"/></svg>

<footer class="footer">
  <div class="f-col" style="left:117px">Tallow Crate Rentals - Australia Wide<br>Sydney<br>Melbourne<br>Brisbane<br>Perth<br>Adelaide<br>Canberra</div>
  <div class="f-col" style="left:445px">Learn More<br>Waste Types<br>Skip Bin Sizes<br>Refund Policy<br>Pay Later Plans<br>FAQ<br>Privacy</div>
  <div class="news">Latest Industry News<br>Sign up for the latest news, offers from<br>TALLOW CRATE RENTALS AUSTRALIA</div>
  <div class="sub"><span class="field">Your email</span><span class="go">SUBSCRIBE</span></div>
  <div class="social"><i></i><i></i><i></i><i></i></div>
</footer>
<div class="bottom">
  <p class="copy">Copyright © 2019, TALLOW CRATE RENTALS AUSTRALIA. Powered by Storefront Co</p>
  <div class="pay"><i></i><i></i><i></i><i></i><i></i></div>
</div>

</body>
</html>
```